Online Banner and skyscrapper ads

Design ads for real estate company in Australia to be used on Nest huntr.com.au details below
sizes
Leaderboard Specifications
• Dimensions: 728×90px
• Format: HTML5 or Animated/Static Gif
• Max file size: 100kb (HTML5), 80kb (GIF, JPG, PNG)
• Back-up image: 40kb (GIF, JPG, PNG). Back-up image only required if you supply an HTML5 banner.
• Looping: Yes
• See Leaderboard for more information.
Email Alert Strip Ad (EASA) Specifications
• Dimensions: 472×114 px
• Format: JPEG, PNG or Static GIF
• File Size: 20kb
• Looping: No
Skyscraper Specifications
• Dimensions: 160x600px
• Looping: Yes
• See Skyscraper for more information.
Mega Skyscraper Specifications
• Dimensions: 300x600px
• Format: HTML5 or Animated/Static GIF
• File size: 100kb (Html5) or 80kb (GIF, JPG, PNG)
• Back-up image: 40kb (JPG or PNG). Back-up image only required if you supply an HTML5 banner.
• Looping: Yes
• See Half Page for more information.

I would like them to be quite simple , TREVANCE Your Faulconbridge property experts and another saying TREVANCE your Lawson property experts and TREVANCE your Hazelbrook property experts (3 different versions all up ) and another version MOIRA DELVINE your Faulconbridge property expert with logo and her image , i've put a photo of the top banner example and a video of the side banner it has a video in the background that i will get produced if it works

```html
<!DOCTYPE html>
<html lang="en">
<head>
<meta charset="utf-8">
<title>TREVANCE – Mega Skyscraper Ads</title>
<link rel="stylesheet" href="https://fonts.googleapis.com/css2?family=Montserrat:wght@300;400;500;600&display=swap">
<style>
  :root {
    --page-bg: #eef0f3;
    --sky-top: #343d52;
    --sky-mid: #4a566d;
    --horizon: #66758b;
    --hills: #2c3a47;
    --forest: #1a262c;
    --forest-deep: #111a1e;
    --ink-light: #f4f6f8;
    --ink-soft: #d7dde4;
  }
  * { box-sizing: border-box; margin: 0; padding: 0; }
  html, body {
    width: 1200px;
    height: 861px;
    overflow: hidden;
    background: var(--page-bg);
    font-family: "Montserrat", sans-serif;
  }
  .ad-set {
    width: 1200px;
    height: 861px;
    display: flex;
    justify-content: center;
    align-items: center;
    gap: 60px;
  }
  .skyscraper {
    position: relative;
    width: 300px;
    height: 600px;
    overflow: hidden;
    box-shadow: 0 2px 8px rgba(20, 30, 40, 0.18);
  }
  .skyscraper__backdrop {
    position: absolute;
    inset: 0;
    background: linear-gradient(
      to bottom,
      var(--sky-top) 0%,
      var(--sky-mid) 28%,
      var(--horizon) 44%,
      var(--hills) 52%,
      var(--forest) 70%,
      var(--forest-deep) 100%
    );
  }
  .skyscraper__content {
    position: relative;
    height: 100%;
    display: flex;
    flex-direction: column;
    align-items: center;
    color: var(--ink-light);
    text-align: center;
  }
  .brand {
    margin-top: 178px;
    display: flex;
    flex-direction: column;
    align-items: center;
  }
  .brand__mark {
    width: 18px;
    height: 18px;
    background: var(--ink-light);
    margin-bottom: 22px;
  }
  .brand__name {
    font-size: 31px;
    font-weight: 400;
    letter-spacing: 3px;
    line-height: 1;
  }
  .brand__since {
    margin-top: 14px;
    font-size: 9px;
    font-weight: 400;
    letter-spacing: 3px;
    color: var(--ink-soft);
  }
  .tagline {
    margin-top: 52px;
    line-height: 1.12;
  }
  .tagline__lead {
    display: block;
    font-size: 27px;
    font-weight: 300;
  }
  .tagline__suburb {
    display: block;
    font-size: 29px;
    font-weight: 500;
  }
  .tagline__role {
    display: block;
    font-size: 25px;
    font-weight: 500;
  }
</style>
</head>
<body>
  <main class="ad-set">

    <article class="skyscraper">
      <div class="skyscraper__backdrop" role="img" aria-label="Background footage: misty blue dusk sky over a forested mountain valley"></div>
      <div class="skyscraper__content">
        <div class="brand">
          <span class="brand__mark"></span>
          <span class="brand__name">TREVANCE</span>
          <span class="brand__since">SINCE 1987</span>
        </div>
        <p class="tagline">
          <span class="tagline__lead">Your</span>
          <span class="tagline__suburb">Faulconbridge</span>
          <span class="tagline__role">Property Experts</span>
        </p>
      </div>
    </article>

    <article class="skyscraper">
      <div class="skyscraper__backdrop" role="img" aria-label="Background footage: misty blue dusk sky over a forested mountain valley"></div>
      <div class="skyscraper__content">
        <div class="brand">
          <span class="brand__mark"></span>
          <span class="brand__name">TREVANCE</span>
          <span class="brand__since">SINCE 1987</span>
        </div>
        <p class="tagline">
          <span class="tagline__lead">Your</span>
          <span class="tagline__suburb">Hazelbrook</span>
          <span class="tagline__role">Property Experts</span>
        </p>
      </div>
    </article>

    <article class="skyscraper">
      <div class="skyscraper__backdrop" role="img" aria-label="Background footage: misty blue dusk sky over a forested mountain valley"></div>
      <div class="skyscraper__content">
        <div class="brand">
          <span class="brand__mark"></span>
          <span class="brand__name">TREVANCE</span>
          <span class="brand__since">SINCE 1987</span>
        </div>
        <p class="tagline">
          <span class="tagline__lead">Your</span>
          <span class="tagline__suburb">Lawson</span>
          <span class="tagline__role">Property Experts</span>
        </p>
      </div>
    </article>

  </main>
</body>
</html>
```